Commercial Real Estate

We need a business card design for a new commercial real estate business that specializes in apartment building brokerage. Not individual units but the entire complex. We find and represent the owners existing buildings and well as new buyers for those buildings. The design should convey trust, integrity, knowledge and growth. It should be easily read.

Target Market(s)

40 to 65 years old

Industry/Entity Type

Real Estate

```html
<!DOCTYPE html>
<html lang="en">
<head>
<meta charset="utf-8">
<title>Trellway Property Investments – Business Card</title>
<link rel="stylesheet" href="https://fonts.googleapis.com/css2?family=Questrial&display=swap">
<style>
  :root {
    --backdrop: #e9ebec;
    --card: #ffffff;
    --teal-light: #7fd3d2;
    --teal: #4cb8b7;
    --teal-deep: #2e9fa0;
    --slate: #61696c;
    --slate-soft: #7d8588;
    --white: #ffffff;
  }
  * { box-sizing: border-box; margin: 0; padding: 0; }
  html, body {
    width: 1200px; height: 900px; overflow: hidden;
    background: var(--backdrop);
    font-family: "Questrial", "Century Gothic", sans-serif;
  }
  .business-card {
    position: absolute; left: 75px; top: 150px;
    width: 1050px; height: 600px;
    background: var(--card);
    box-shadow: 0 18px 40px rgba(0,0,0,.18);
    overflow: hidden;
  }
  .skyline-band { position: absolute; inset: 0; width: 100%; height: 100%; }
  .agent {
    position: absolute; right: 56px; top: 58px; text-align: right; color: var(--slate);
  }
  .agent-name { font-size: 44px; letter-spacing: .5px; line-height: 1.1; }
  .agent-title { font-size: 24px; color: var(--slate-soft); margin-top: 4px; }
  .brand {
    position: absolute; left: 520px; top: 250px;
    display: flex; align-items: center; gap: 18px;
    color: var(--slate);
  }
  .brand-dot { width: 26px; height: 26px; border-radius: 50%; background: var(--teal); flex: none; }
  .brand-name { font-size: 52px; line-height: 1; letter-spacing: 1px; }
  .brand-name span { display: block; font-size: 52px; }
  .contact-list {
    position: absolute; left: 44px; top: 330px; list-style: none; color: var(--white);
    font-size: 28px; line-height: 1.25;
  }
  .contact-item { display: flex; align-items: flex-start; gap: 20px; margin-bottom: 16px; }
  .contact-icon { width: 30px; height: 30px; flex: none; margin-top: 2px; }
</style>
</head>
<body>
  <main class="business-card">
    <svg class="skyline-band" viewBox="0 0 1050 600" role="img" aria-label="Teal city skyline silhouette rising from the lower edge">
      <defs>
        <linearGradient id="teal-fade" x1="0" y1="0" x2="0" y2="1">
          <stop offset="0" stop-color="var(--teal-light)"/>
          <stop offset="1" stop-color="var(--teal-deep)"/>
        </linearGradient>
      </defs>
      <path d="M0 260 C180 250 360 270 460 320 C560 370 620 470 700 600 L0 600 Z" fill="url(#teal-fade)"/>
    </svg>

    <header class="agent">
      <p class="agent-name">Your Name</p>
      <p class="agent-title">Boker / Salesperson</p>
    </header>

    <div class="brand">
      <span class="brand-dot"></span>
      <p class="brand-name">Trellway<span>Property Investments</span></p>
    </div>

    <ul class="contact-list">
      <li class="contact-item">
        <svg class="contact-icon" viewBox="0 0 24 24"><path d="M12 2a7 7 0 0 0-7 7c0 5 7 13 7 13s7-8 7-13a7 7 0 0 0-7-7zm0 9.5A2.5 2.5 0 1 1 12 6.5a2.5 2.5 0 0 1 0 5z" fill="#fff"/></svg>
        <span>Your Complete,<br>Address Details Here</span>
      </li>
      <li class="contact-item">
        <svg class="contact-icon" viewBox="0 0 24 24"><path d="M6.6 10.8a15 15 0 0 0 6.6 6.6l2.2-2.2a1 1 0 0 1 1-.25 11.4 11.4 0 0 0 3.6.6 1 1 0 0 1 1 1V20a1 1 0 0 1-1 1A17 17 0 0 1 3 4a1 1 0 0 1 1-1h3.5a1 1 0 0 1 1 1c0 1.25.2 2.45.6 3.6a1 1 0 0 1-.25 1z" fill="#fff"/></svg>
        <span>702-555-0186</span>
      </li>
      <li class="contact-item">
        <svg class="contact-icon" viewBox="0 0 24 24"><rect x="2" y="5" width="20" height="14" rx="1" fill="#fff"/><path d="M2.5 5.5 12 13l9.5-7.5" fill="none" stroke="#3aa9a9" stroke-width="1.6"/></svg>
        <span>Jordan@trellwayprop.com</span>
      </li>
      <li class="contact-item">
        <svg class="contact-icon" viewBox="0 0 24 24"><circle cx="12" cy="12" r="9.5" fill="none" stroke="#fff" stroke-width="2"/><path d="M2.5 12h19M12 2.5c3 3 3 16 0 19M12 2.5c-3 3-3 16 0 19" fill="none" stroke="#fff" stroke-width="1.6"/></svg>
        <span>www.TrellwayPropertyLV.com</span>
      </li>
    </ul>
  </main>
</body>
</html>
```